New name flyer

We have just changed our business name from kR Property group to Harbor Lantern. We want to distribute a flyer to the local community to inform them of the change. We are a realestate agency which focuses mainly on property management but also sales. We service from Brisbane to the Sunshine coast.

Target Market(s)

Local community

Industry/Entity Type

realestate

Requirements
Must have
• Details of name change
Nice to have
• Servicing area Brisbane and Sunshine Coast, no change in management or services we offer, and will continue pride ourselves on offering a high level of service, with the same team from the Gold to Sunshine Coast.
Should not have
• too much wording.

```html
<!DOCTYPE html>
<html lang="en">
<head>
<meta charset="utf-8">
<title>Harbor Lantern – New Name Flyer</title>
<link href="https://fonts.googleapis.com/css2?family=Questrial&family=Roboto+Condensed:wght@300;400;700&display=swap" rel="stylesheet">
<style>
  :root {
    --navy: #001862;
    --gold: #c89300;
    --white: #ffffff;
  }
  html, body {
    margin: 0;
    padding: 0;
    overflow: hidden;
    background: var(--navy);
  }
  .flyer {
    position: relative;
    width: 825px;
    height: 1200px;
    background: var(--navy);
    overflow: hidden;
    font-family: "Roboto Condensed", "Arial Narrow", sans-serif;
  }
  .brand-name {
    position: absolute;
    left: 53px;
    top: 360px;
    margin: 0;
    color: var(--white);
    font-weight: 700;
    font-size: 50px;
    line-height: 56px;
    letter-spacing: 3px;
    text-transform: uppercase;
  }
  .headline {
    position: absolute;
    left: 446px;
    top: 322px;
    margin: 0;
    color: var(--gold);
    font-family: "Questrial", sans-serif;
    font-weight: 400;
    font-size: 64px;
    line-height: 72px;
  }
  .announcement {
    position: absolute;
    left: 52px;
    top: 712px;
    margin: 0;
    color: var(--white);
    font-weight: 300;
    font-size: 38px;
    line-height: 45px;
  }
  .announcement .new-name {
    display: block;
    margin-top: 4px;
    color: var(--gold);
    font-weight: 700;
    font-size: 52px;
    line-height: 56px;
    letter-spacing: -0.5px;
    text-transform: uppercase;
  }
  .service-box {
    position: absolute;
    left: 440px;
    top: 646px;
    width: 385px;
    height: 282px;
    box-sizing: border-box;
    padding: 18px 10px 0 18px;
    background: var(--gold);
    color: var(--navy);
    font-weight: 400;
    font-size: 22px;
    line-height: 31.4px;
  }
  .service-box p { margin: 0; }
  .tagline {
    position: absolute;
    left: 0;
    width: 825px;
    top: 1056px;
    margin: 0;
    text-align: center;
    color: var(--gold);
    font-weight: 300;
    font-size: 31px;
  }
</style>
</head>
<body>
  <main class="flyer">
    <p class="brand-name">Harbor<br>Lantern</p>

    <h1 class="headline">We've<br>Changed.</h1>

    <h2 class="announcement">kR Property group<br>is now
      <span class="new-name">Harbor Lantern.</span>
    </h2>

    <section class="service-box">
      <p>We service from<br>
      Brisbane to the Sunshine coast.<br>
      No change in management<br>
      or services we offer,<br>
      and will continue pride ourselves<br>
      on offering a high level of service,<br>
      with the same team from the<br>
      Gold to Sunshine Coast.</p>
    </section>

    <p class="tagline">Change for a better tomorrow.</p>
  </main>
</body>
</html>
```